New Innovative Counselling and psychotherapy Service needs Business Card design

Keep it simple and professional. On one side, just company name and logo (perhaps in all blue) and maybe a tag line.

On other side (all white) my name and Qualifications in centre

Industry/Entity Type

Health And Wellness

Contact Information for Business Card

Dara Whelby
Counsellor & Psychotherapist
BSc (Psychol.), BA, Dip. (Couns. & Psych.), PG.Cert (CBT), FGTrK, ONRE

I will also require Mobile no, Email and web site address of which I'll pass on to final designer.

Font styles to use
Sans Serif

Requirements
Must have
• My Logo Only and please use the colours in logo that is in it.
Should not have
• Any other images

```html
<!DOCTYPE html>
<html lang="en">
<head>
<meta charset="utf-8">
<title>Brightwell Lane – Business Card</title>
<link rel="stylesheet" href="https://fonts.googleapis.com/css2?family=Montserrat:wght@400;500;600&display=swap">
<style>
  :root {
    --canvas: #e9eaec;
    --brand-blue: #4fb3e6;
    --brand-green: #8cc63f;
    --ink: #2b2b2b;
    --paper: #ffffff;
    --card-radius: 16px;
  }
  * { box-sizing: border-box; margin: 0; padding: 0; }
  html, body {
    width: 1200px; height: 930px; overflow: hidden;
    background: var(--canvas);
    font-family: "Montserrat", sans-serif;
  }
  .stage { position: relative; width: 1200px; height: 930px; }
  .card {
    position: absolute; width: 560px; height: 320px;
    border-radius: var(--card-radius);
    box-shadow: 0 8px 24px rgba(0,0,0,.12);
  }

  /* Front */
  .card--front {
    left: 70px; top: 70px;
    background: var(--brand-blue);
    color: var(--paper);
    display: flex; flex-direction: column; align-items: center; justify-content: center;
  }
  .front-brand { display: flex; flex-direction: column; align-items: center; gap: 18px; margin-top: -20px; }
  .front-brand__dot { width: 86px; height: 86px; border-radius: 50%; background: var(--paper); }
  .front-brand__name { font-size: 30px; font-weight: 400; letter-spacing: .5px; }
  .front-web {
    position: absolute; bottom: 34px; left: 0; right: 0;
    text-align: center; font-size: 13px; letter-spacing: .5px;
  }

  /* Back */
  .card--back { left: 570px; top: 540px; background: var(--paper); color: var(--ink); }
  .brand {
    position: absolute; right: 38px; top: 36px;
    display: flex; align-items: center; gap: 12px;
  }
  .brand__dot { width: 34px; height: 34px; border-radius: 50%; background: var(--brand-blue); }
  .brand__name { font-size: 21px; font-weight: 400; color: var(--ink); }

  .person { position: absolute; left: 40px; top: 110px; }
  .person__name {
    font-size: 29px; font-weight: 500; color: var(--brand-blue);
    text-transform: uppercase; letter-spacing: .3px; line-height: 1.05;
  }
  .person__role, .person__quals { font-size: 12.5px; line-height: 1.4; }
  .person__role { margin-top: 4px; }

  .divider {
    position: absolute; left: 40px; right: 40px; top: 222px;
    height: 2px; background: var(--brand-green);
  }

  .contacts { position: absolute; left: 40px; top: 236px; list-style: none; }
  .contacts li {
    display: flex; align-items: center; gap: 10px;
    font-size: 13px; line-height: 22px;
  }
  .contacts svg { width: 11px; height: 11px; flex: none; }
  .contacts .accent { color: var(--brand-blue); }
</style>
</head>
<body>
<main class="stage">

  <section class="card card--front" aria-label="Card front">
    <div class="front-brand">
      <span class="front-brand__dot"></span>
      <span class="front-brand__name">Brightwell Lane</span>
    </div>
    <p class="front-web">www.brightwelllane.com</p>
  </section>

  <section class="card card--back" aria-label="Card back">
    <div class="brand">
      <span class="brand__dot"></span>
      <span class="brand__name">Brightwell Lane</span>
    </div>

    <div class="person">
      <h1 class="person__name">Dara Whelby</h1>
      <p class="person__role">Counsellor &amp; Psychotherapist</p>
      <p class="person__quals">BSc (Psychol.), BA, Dip. (Couns. &amp; Psych.), PG.Cert<br>(CBT), FGTrK, ONRE</p>
    </div>

    <div class="divider"></div>

    <ul class="contacts">
      <li>
        <svg viewBox="0 0 12 12" aria-hidden="true"><path d="M3 1l2 2.5-1 1.2c.6 1.3 1.6 2.3 2.9 2.9l1.2-1L11 8.6 9.8 10.5C5.5 10.5 1.5 6.5 1.5 2.2z" fill="var(--brand-blue)"/></svg>
        888-555-0147
      </li>
      <li>
        <svg viewBox="0 0 12 12" aria-hidden="true"><rect x="1" y="2.5" width="10" height="7" rx="1" fill="none" stroke="var(--brand-blue)" stroke-width="1.2"/><path d="M1.5 3l4.5 3.5L10.5 3" fill="none" stroke="var(--brand-blue)" stroke-width="1.2"/></svg>
        info@brightwelllane.com
      </li>
      <li>
        <svg viewBox="0 0 12 12" aria-hidden="true"><circle cx="6" cy="6" r="4.8" fill="none" stroke="var(--brand-blue)" stroke-width="1.1"/><ellipse cx="6" cy="6" rx="2" ry="4.8" fill="none" stroke="var(--brand-blue)" stroke-width="1"/><path d="M1.2 6h9.6" stroke="var(--brand-blue)" stroke-width="1"/></svg>
        <span>www.<span class="accent">brightwelllane</span>.com</span>
      </li>
    </ul>
  </section>

</main>
</body>
</html>
```